Telecommunications/Power civil contractor needs business card design

Were a new telecommunications/power underground civil contractor that is looking for a new business card design. Our company colours are silver or grey and orange. Feel free to use the white background logo or the black background logo.

Target Market(s)

Local contractors, utility companies, private sector mining/energy companies, developers.

Industry/Entity Type

Telecommunications

Contact Information for Business Card

Each card will need the following info:
Persons name:
Title:
E-mail:
Phone number:
Shop Address:
Mailing Address:

Requirements
Must have
• Each card will need the following info:
• Persons name:
• Title:
• E-mail:
• Phone number:
• Shop Address:
• Mailing Address:

```html
<!DOCTYPE html>
<html lang="en">
<head>
<meta charset="utf-8">
<title>Ridgeline Conduit Inc — Business Card</title>
<link rel="stylesheet" href="https://fonts.googleapis.com/css2?family=Open+Sans:wght@400;600;700&display=swap">
<style>
  :root {
    --stage: #2b2b2b;
    --card-black: #111111;
    --card-white: #ffffff;
    --brand-orange: #f05a22;
    --brand-grey: #8a8a8a;
    --brand-grey-dark: #5e5e5e;
    --title-grey: #6b6b6b;
    --text-light: #ffffff;
  }
  * { box-sizing: border-box; margin: 0; padding: 0; }
  html, body {
    width: 1200px; height: 900px; overflow: hidden;
    background: var(--stage);
    font-family: "Open Sans", Arial, sans-serif;
  }
  .stage { position: relative; width: 1200px; height: 900px; }

  .card {
    position: absolute; width: 520px; height: 300px;
    border-radius: 3px; overflow: hidden;
    box-shadow: 0 14px 30px rgba(0,0,0,.45);
  }

  /* Back of card */
  .card-back {
    left: 70px; top: 110px;
    background: var(--card-black);
    display: flex; align-items: center; justify-content: center;
  }
  .back-mark { display: flex; align-items: center; gap: 16px; }
  .mark-ring {
    width: 54px; height: 54px; border-radius: 50%;
    border: 5px solid var(--brand-grey);
  }
  .back-name {
    color: var(--brand-orange); font-weight: 700;
    font-size: 26px; letter-spacing: 1px; text-transform: uppercase;
  }

  /* Front of card */
  .card-front { left: 610px; top: 470px; background: var(--card-white); }
  .front-curve { position: absolute; inset: 0; }
  .front-brand {
    position: absolute; left: 0; width: 470px; top: 26px;
    display: flex; flex-direction: column; align-items: center; gap: 8px;
  }
  .brand-ring {
    width: 48px; height: 48px; border-radius: 50%;
    border: 5px solid var(--brand-grey);
  }
  .brand-name {
    color: var(--brand-orange); font-weight: 700;
    font-size: 17px; letter-spacing: .5px; text-transform: uppercase;
    text-align: center; line-height: 1.15; white-space: nowrap;
  }
  .person {
    position: absolute; right: 265px; top: 218px; text-align: right;
    white-space: nowrap;
  }
  .person-name { color: var(--text-light); font-weight: 700; font-size: 20px; line-height: 1.25; }
  .person-title { color: var(--title-grey); font-size: 14px; }
  .contact-divider {
    position: absolute; left: 270px; top: 202px; width: 1px; height: 74px;
    background: rgba(255,255,255,.45);
  }
  .contact {
    position: absolute; left: 282px; top: 200px;
    color: var(--text-light); font-size: 13px; line-height: 1.5;
    list-style: none; white-space: nowrap;
  }
  .contact li { display: flex; align-items: center; gap: 6px; }
  .contact svg { flex: none; }
</style>
</head>
<body>
<main class="stage">

  <section class="card card-back" aria-label="Card back">
    <div class="back-mark">
      <span class="mark-ring"></span>
      <span class="back-name">Ridgeline Conduit</span>
    </div>
  </section>

  <section class="card card-front" aria-label="Card front">
    <svg class="front-curve" width="520" height="300" viewBox="0 0 520 300">
      <path d="M0 180 L222 180 L237 194 L252 180 Q420 162 520 100 L520 300 L0 300 Z" fill="var(--brand-orange)"/>
      <path d="M0 166 L222 166 L237 180 L252 166 Q420 148 520 86 L520 94 Q420 156 252 174 L237 188 L222 174 L0 174 Z" fill="var(--brand-grey-dark)"/>
    </svg>

    <div class="front-brand">
      <span class="brand-ring"></span>
      <span class="brand-name">Ridgeline Conduit Inc</span>
    </div>

    <div class="person">
      <p class="person-name">Marlow Trent</p>
      <p class="person-title">Managing Director</p>
    </div>

    <span class="contact-divider"></span>
    <ul class="contact">
      <li>N. 40 Alder Road,</li>
      <li>Suite 200, Ridgeton, WA 55501</li>
      <li>
        <svg width="13" height="13" viewBox="0 0 14 14" aria-hidden="true">
          <circle cx="7" cy="7" r="7" fill="var(--card-white)"/>
          <path d="M4.5 3.5 L6 5.5 L5.2 6.5 Q6 8 7.5 8.8 L8.5 8 L10.5 9.5 L9.6 10.7 Q5 10 3.3 4.4 Z" fill="var(--brand-orange)"/>
        </svg>
        555.010.2468
      </li>
      <li>
        <svg width="13" height="13" viewBox="0 0 14 14" aria-hidden="true">
          <circle cx="7" cy="7" r="7" fill="var(--card-white)"/>
          <rect x="3.5" y="4.5" width="7" height="5" fill="none" stroke="var(--brand-orange)" stroke-width="1.1"/>
          <path d="M3.5 4.5 L7 7.3 L10.5 4.5" fill="none" stroke="var(--brand-orange)" stroke-width="1.1"/>
        </svg>
        info@ridgelineconduit.com
      </li>
    </ul>
  </section>

</main>
</body>
</html>
```